Flyer-Design für Musikverein - Jugendkapelle
Zielgruppe
Musikverein Kolmsried
Unsere Zielgruppe sind Kinder und Jugendliche, die ein Instrument erlernen wollen.
Der Einstieg der jüngsten geht in einem Alter ab ca. 8 Jahren los. Die meisten neuen Musiker steigen zwischen 10 - 14 Jahren ein.
Der Flyer soll aber auch geeignet sein um an Grund- und weiterführenden Schulen ausgelegt werden zu können um Musiker für die Jugendkapelle zu gewinnen. Dementsprechend frisch und interessant soll der Flyer gestaltet sein.
Aufgabenstellung
Es soll ansprechend sein für Jugendliche, frisch, fröhlich und soll das Interesse der jugendlichen mit dem Design wecken.
Es soll die Jugendlichkeit, die Blasmusik und das Vereinsleben miteinander verbinden, sowie die Vorteile und der Spaß an der Musik (Instrument erlernen, Spaß am Musizieren, neue Freunde und Kameradschaft und auch Freizeitaktivitäten) miteinander darstellen.

```html
<!DOCTYPE html>
<html lang="de">
<head>
<meta charset="utf-8">
<title>Musikverein Kolmsried – Jugendkapelle Flyer</title>
<link rel="stylesheet" href="https://fonts.googleapis.com/css2?family=Rajdhani:wght@700&family=Lato:ital,wght@0,300;0,400;0,700;0,900;1,900&family=Heebo:wght@300&display=swap">
<style>
  :root {
    --backdrop: #e7e4df;
    --paper: #ffffff;
    --ink: #111111;
    --rule: #5b1a2c;
    --band: #000000;
    --band-text: #ffffff;
    --muted: #444444;
  }
  * { margin: 0; padding: 0; box-sizing: border-box; }
  html, body {
    width: 1200px; height: 798px; overflow: hidden;
    background: var(--backdrop);
  }
  .canvas { position: relative; width: 1200px; height: 798px; }

  .flyer {
    position: absolute;
    width: 534px; height: 534px;
    background: var(--paper);
    box-shadow: 0 2px 6px rgba(0,0,0,.12);
  }
  .flyer--front { left: 64px; top: 200px; }
  .flyer--back  { left: 634px; top: 70px; width: 532px; height: 532px; }

  .rule {
    position: absolute; left: 0; right: 0;
    height: 1px; background: var(--rule);
  }

  /* Front side */
  .front__headline {
    position: absolute; left: 0; right: 0; top: 165px;
    text-align: center;
    font-family: "Rajdhani", "Arial Narrow", sans-serif;
    font-weight: 700; font-size: 39px; letter-spacing: .5px;
    color: var(--ink); line-height: 46px;
  }
  .front__photo {
    position: absolute; left: 0; right: 0; top: 224px; height: 189px;
    background: linear-gradient(100deg, #a9a59a 0%, #e9e6e2 30%, #d8d3cf 55%, #cfc8c6 75%, #8f8a8c 100%);
  }
  .front__band {
    position: absolute; left: 0; right: 0; top: 427px; height: 37px;
    background: var(--band);
    color: var(--band-text);
    font-family: "Heebo", "Helvetica Neue", sans-serif;
    font-weight: 300; font-size: 23px; line-height: 37px;
    text-align: center;
  }

  .footer {
    position: absolute; left: 0; right: 0; bottom: 17px;
    text-align: center;
    font-family: "Lato", sans-serif; font-weight: 300;
    font-size: 11px; color: var(--muted);
  }

  /* Back side */
  .back__photos {
    position: absolute; left: 0; right: 0; top: 64px; height: 118px;
    display: flex;
  }
  .back__photo { height: 100%; }
  .back__photo--sax { width: 177px; background: radial-gradient(circle at 60% 55%, #c89a3c 0%, #6b4a17 35%, #0c0906 70%); }
  .back__photo--flute { width: 182px; background: linear-gradient(120deg, #ecebe8 0%, #cfd0d2 45%, #6f7378 55%, #e4e3e0 80%); }
  .back__photo--trumpet { width: 173px; background: radial-gradient(circle at 60% 50%, #e7c67a 0%, #b57c34 40%, #7d5233 75%, #c9b9a9 100%); }

  .back__content {
    position: absolute; left: 68px; right: 56px; top: 226px;
    font-family: "Lato", sans-serif; color: var(--ink);
    font-size: 11.2px; line-height: 13.6px;
  }
  .back__heading {
    font-family: "Rajdhani", "Arial Narrow", sans-serif;
    font-weight: 700; font-size: 21px; line-height: 24px;
    letter-spacing: .2px; margin-bottom: 12px;
  }
  .back__lead { font-weight: 900; margin-bottom: 9px; }
  .back__text { margin-bottom: 13px; }
  .back__text strong { font-weight: 900; }
  .back__cta { font-weight: 900; font-style: italic; display: block; }
</style>
</head>
<body>
<div class="canvas">

  <section class="flyer flyer--front">
    <div class="rule" style="top:164px"></div>
    <h1 class="front__headline">MUSIK MACHT FREU(N)DE.</h1>
    <div class="rule" style="top:211px"></div>
    <div class="front__photo" role="img" aria-label="Foto: Jugendliche spielen Klarinette und Saxophon im Orchester"></div>
    <div class="front__band">Wer will Musiker&nbsp; werden?</div>
    <p class="footer">Musikverein Kolmsried - www.kolmsried-blasmusik.de</p>
  </section>

  <section class="flyer flyer--back">
    <div class="rule" style="top:53px"></div>
    <div class="back__photos">
      <div class="back__photo back__photo--sax" role="img" aria-label="Foto: goldenes Saxophon vor dunklem Hintergrund"></div>
      <div class="back__photo back__photo--flute" role="img" aria-label="Foto: Querflöte auf Notenblättern"></div>
      <div class="back__photo back__photo--trumpet" role="img" aria-label="Foto: Trompete in Nahaufnahme"></div>
    </div>
    <div class="rule" style="top:192px"></div>

    <div class="back__content">
      <h2 class="back__heading">HAST DU LUST BEI UNS MITZUMACHEN?</h2>
      <p class="back__lead">Wir bieten im Bereich Blasmusik qualifizierten Musikunterricht für Kinder und Jugendliche an. Unsere Leistungen sind Einzelunterricht, Lehrkräfte mit Musikausbildung und langjähriger pädagogischer Erfahrung.</p>
      <p class="back__text">Der Musikverein Kolmsried e.V. bietet allen musikinteressierten Kindern, Jugendlichen und Erwachsenen die Möglichkeit ein Instrument zu erlernen. Bei uns kannst du <strong>Trompete/Flügelhorn, Tuba, Tenorhorn/Bariton/Posaune, Waldhorn, Klarinette, Saxophon, Querflöte und Schlagzeug</strong> lernen.</p>
      <p class="back__text">In unserer Jugendkapelle haben die Kinder und Jugendlichen die Möglichkeit nach 1-2 jähriger Ausbildung in der Gruppe zu spielen und zu üben. Danach geht es an das Musizieren im großen Orchester. Letztendlich entscheiden die Dirigenten und Ausbilder über den Eintritt in die jeweiligen Orchester.
        <span class="back__cta">Oder du kannst schon ein Instrument spielen und willst mit anderen gemeinsam musizieren? Dann komm doch in die Jugendkapelle „TAKTWECHSEL“.</span></p>
    </div>
    <p class="footer">Musikverein Kolmsried - www.kolmsried-blasmusik.de</p>
  </section>

</div>
</body>
</html>
```